NCBG website design

We need a page template website design for a cms website. Please see the brief attached for the details.
The client is the National Copperfleece Breeders Guild which is an organisation promoting the Copperfleece Sheep Breed within Australia.
Updates

Project Deadline Extended
Reason: So that my top few designs can make changes and re-submit.

Target Market(s)

See attached brief

```html
<!DOCTYPE html>
<html lang="en">
<head>
<meta charset="utf-8">
<title>National Copperfleece Breeders Guild</title>
<link rel="stylesheet" href="https://fonts.googleapis.com/css2?family=Source+Sans+3:wght@400;600;700&family=Arimo:wght@400;700&display=swap">
<style>
:root{
  --green:#1f9a4a;
  --green-dark:#17763a;
  --hero:#3ea868;
  --yellow:#f5c334;
  --gold:#d9a12a;
  --ink:#333;
  --grey:#555;
  --panel:#e6e6e6;
  --line:#cfcfcf;
  --footer:#1d1d1d;
  --white:#fff;
}
*{margin:0;padding:0;box-sizing:border-box}
html,body{width:1029px;height:1200px;overflow:hidden;background:var(--white)}
body{position:relative;font-family:"Arimo",Arial,sans-serif;color:var(--ink)}
.abs{position:absolute}
.head-font{font-family:"Source Sans 3",Arial,sans-serif}

/* header */
.brand{left:86px;top:28px;display:flex;align-items:center;gap:10px}
.brand-mark{width:44px;height:44px;background:var(--green)}
.brand-name{font-family:"Source Sans 3",sans-serif;font-weight:700;font-size:30px;color:var(--green)}
.call{right:92px;top:26px;font-family:"Source Sans 3",sans-serif;font-size:11px;color:var(--ink);display:flex;align-items:center;gap:4px}
.call b{font-size:19px;font-weight:400}
.follow{right:92px;top:62px;font-family:"Source Sans 3",sans-serif;font-size:12px}
.follow-icons{right:86px;top:81px;display:flex;gap:5px}
.follow-icons span{width:19px;height:19px;border-radius:3px;background:#4a73b5}
.follow-icons span:nth-child(3){background:#2d7bb8}
.follow-icons span:nth-child(4){background:#e06a1a}
.follow-icons span:nth-child(5){background:#8796a8}
.follow-icons span:nth-child(6){background:#444}

/* nav */
.nav{left:0;top:113px;width:1029px;height:40px;background:var(--yellow)}
.nav ul{list-style:none;position:absolute;left:100px;top:5px;display:flex;align-items:center;font-family:"Source Sans 3",sans-serif;font-size:12.5px;color:var(--white)}
.nav li{height:29px;line-height:29px;text-align:center}
.nav .active{width:73px;background:#2a2a2a;border-radius:3px}
.nav .sep{width:1px;height:12px;background:var(--white);margin:0 1px}

/* hero */
.hero{left:0;top:153px;width:1029px;height:514px;background:linear-gradient(180deg,#3a9f61 0%,#48ad70 40%,#3c9f63 100%)}
.hero-title{left:0;width:1029px;top:276px;text-align:center;font-family:"Source Sans 3",sans-serif;font-weight:600;font-size:34px;letter-spacing:1px;color:var(--white)}
.hero-text{left:160px;width:709px;top:320px;text-align:center;font-size:15.5px;line-height:21px;color:var(--white)}

/* main panel */
.sheet{left:86px;top:478px;width:857px;height:575px;background:var(--white);border-radius:5px 5px 0 0;box-shadow:0 0 3px rgba(0,0,0,.08)}
.card{top:419px;width:185px;height:237px;background:linear-gradient(180deg,#dcdcdc 0,#efefef 55px,#fbfbfb 120px,#f5f5f5 100%);border-top:7px solid var(--yellow);box-shadow:0 1px 3px rgba(0,0,0,.12);border-radius:0 0 4px 4px;text-align:center}
.card .ring{position:absolute;left:50%;top:35px;width:84px;height:84px;margin-left:-42px;border-radius:50%;background:var(--white);border:8px solid #ececec;display:flex;align-items:center;justify-content:center}
.card h3{position:absolute;left:0;right:0;top:148px;font-family:"Source Sans 3",sans-serif;font-weight:700;font-size:16px;color:var(--ink)}
.card p{position:absolute;left:0;right:0;top:170px;font-size:14.5px;color:var(--grey)}
.card a{position:absolute;left:0;right:0;top:194px;font-size:9.5px;font-style:italic;color:var(--gold);text-decoration:none}

/* tabs */
.tab{top:700px;height:37px;background:linear-gradient(#e9e9e9,#d8d8d8);border:1px solid var(--line);border-bottom:none;font-family:"Source Sans 3",sans-serif;font-size:16px;color:#555;padding-left:16px;line-height:36px}
.tab.current{background:linear-gradient(#2c8a4c,#7fbf90);color:var(--white);border-color:#2c8a4c}
.tab-body{left:111px;top:737px;width:809px;height:208px;background:linear-gradient(#eaeaea,#e3e3e3);border:1px solid var(--line);border-radius:0 0 4px 4px}
.photo{left:119px;top:768px;width:184px;height:141px;border:6px solid var(--yellow);background:linear-gradient(180deg,#5b7a3a 0%,#a9a58a 50%,#5f8a33 100%)}
.tab-text{left:321px;top:773px;width:568px;font-size:10.8px;line-height:17.2px;color:#555}
.tab-text p+p{margin-top:17px}
.tab-text strong{color:#444}

/* partner strip */
.partners{left:111px;top:966px;width:806px;height:66px;border-radius:22px;background:linear-gradient(#d6d6d6,#fff 25%,#fff 75%,#d9d9d9);border:1px solid #d0d0d0}
.partners .arrow{position:absolute;top:20px}
.partners ul{list-style:none;position:absolute;left:55px;right:55px;top:0;height:66px;display:flex;align-items:center;justify-content:space-between;font-family:"Source Sans 3",sans-serif;font-weight:700;font-size:15px;color:#2f4b3a}

/* footer */
.footer{left:0;top:1053px;width:1029px;height:137px;background:var(--footer)}
.footer-links{left:0;width:1029px;top:1072px;text-align:center;font-family:"Source Sans 3",sans-serif;font-size:10.5px;color:#bdbdbd;word-spacing:1px}
.footer-links span{margin:0 4px;color:#777}
.social{left:392px;top:1101px;display:flex;gap:7px}
.social span{width:30px;height:30px;border-radius:50%;border:3px solid #e8e8e8;background:#3b5998}
.social span:nth-child(2){background:#2aa3dc}
.social span:nth-child(3){background:#c3271d}
.social span:nth-child(4){background:#d0432f}
.social span:nth-child(5){background:#2e7fb9}
.social span:nth-child(6){background:#c6202a}
.copy{left:0;width:1029px;top:1156px;text-align:center;font-size:10.5px;color:#bdbdbd}
.baseline{left:0;top:1190px;width:1029px;height:10px;background:var(--green)}
</style>
</head>
<body>

<header>
  <div class="abs brand"><span class="brand-mark"></span><span class="brand-name">Copperfleece</span></div>
  <div class="abs call">
    <svg width="11" height="14" viewBox="0 0 11 14"><path d="M3 1 L5 4 L3.5 5.5 C4.5 8 6 9.5 7.5 10.5 L9 9 L11 12 L9 13.5 C5 13 1 8 1.5 3 Z" fill="#333"/></svg>
    Call Us: <b>555-014-2290</b>
  </div>
  <div class="abs follow">Follow Us on:</div>
  <div class="abs follow-icons" aria-label="Social links"><span></span><span></span><span></span><span></span><span></span><span></span></div>
</header>

<nav class="abs nav">
  <ul>
    <li class="active">HOME</li>
    <li style="width:103px">ABOUT US</li><li class="sep"></li>
    <li style="width:123px">MEMBERS</li><li class="sep"></li>
    <li style="width:124px">STUD PAGES</li><li class="sep"></li>
    <li style="width:101px">NEWS</li><li class="sep"></li>
    <li style="width:101px">SALES</li><li class="sep"></li>
    <li style="width:100px">LINK</li><li class="sep"></li>
    <li style="width:104px">CONTACT</li>
  </ul>
</nav>

<section class="abs hero" role="img" aria-label="Flock of sheep in a shearing shed, tinted green"></section>
<h1 class="abs hero-title">NATIONAL COPPERFLEECE BREEDERS GUILD</h1>
<p class="abs hero-text">Lorem Ipsum is simply dummy text of the Ipsum has been the industry's standard dummy text ever since printing and typesetting industry. Lorem Ipsum has been the industry's standard dummy text ever since the 1500s,</p>

<div class="abs sheet"></div>

<div class="abs card" style="left:110px">
  <div class="ring"><svg width="30" height="30" viewBox="0 0 30 30"><circle cx="15" cy="15" r="11" fill="none" stroke="#1f9a4a" stroke-width="2.5"/><circle cx="15" cy="15" r="4" fill="#1f9a4a"/></svg></div>
  <h3>Prime Lamb Helpline</h3><p>Lorem Ipsum dolor.</p><a href="#">read more</a>
</div>
<div class="abs card" style="left:313px">
  <div class="ring"><svg width="28" height="28" viewBox="0 0 28 28"><rect x="2" y="4" width="24" height="22" rx="2" fill="#1f9a4a"/><rect x="5" y="11" width="18" height="12" fill="#fff"/><g fill="#1f9a4a"><rect x="7" y="13" width="3" height="3"/><rect x="12" y="13" width="3" height="3"/><rect x="17" y="13" width="3" height="3"/><rect x="7" y="18" width="3" height="3"/><rect x="12" y="18" width="3" height="3"/><rect x="17" y="18" width="3" height="3"/></g></svg></div>
  <h3>Events</h3><p>Lorem Ipsum dolor.</p><a href="#">read more</a>
</div>
<div class="abs card" style="left:514px">
  <div class="ring"><svg width="28" height="30" viewBox="0 0 28 30"><circle cx="12" cy="8" r="6" fill="#1f9a4a"/><path d="M2 28 C2 18 22 18 22 28 Z" fill="#1f9a4a"/><path d="M20 18 h6 M23 15 v6" stroke="#1f9a4a" stroke-width="2.5"/></svg></div>
  <h3>Members</h3><p>Lorem Ipsum dolor.</p><a href="#">read more</a>
</div>
<div class="abs card" style="left:719px">
  <div class="ring"><svg width="30" height="26" viewBox="0 0 30 26"><rect x="2" y="2" width="26" height="22" rx="2" fill="none" stroke="#1f9a4a" stroke-width="2.5"/><rect x="6" y="7" width="8" height="7" fill="#1f9a4a"/><path d="M17 8h7M17 12h7M6 18h18" stroke="#1f9a4a" stroke-width="2"/></svg></div>
  <h3>Latest News</h3><p>Lorem Ipsum dolor.</p><a href="#">read more</a>
</div>

<div class="abs tab current" style="left:111px;width:129px">Why Us</div>
<div class="abs tab" style="left:244px;width:148px">Copperfleece</div>
<div class="abs tab" style="left:396px;width:148px">Cross Breed</div>
<div class="abs tab" style="left:548px;width:148px">Progency Testing</div>
<div class="abs tab-body"></div>
<div class="abs photo" role="img" aria-label="Sheep standing in green pasture"></div>
<div class="abs tab-text">
  <p><strong>Lorem ipsum dolor sit amet, consectetur adipiscing elit etiam accumsan, ipsum a tristique varius non euismod elit massa vitae odio.</strong> Vestibulum sodales nisi quis nisi imperdiet scelerisque euismod ulum elit odio, eu porta metus aenean Lorem ipsum dolor sit amet, consectetur adipiscing elit etiam accumsan, ipsum a tristique varius non euismod elit massa vitae odio.</p>
  <p>Vestibulum sodales nisi quis nisi imperdiet scelerisque euismod ulum elit odio, eu porta metus aenean posuere hendrerit lacus sit amet venenatis. posuere hendrerit lacus sit amet venenatis.Lorem ipsum dolor sit amet, consectetur adipiscing elit etiam accumsan.quis nisi imperdiet scelerisque euismod ulum elit odio, eu porta metus aenean posuere</p>
</div>

<div class="abs partners">
  <svg class="arrow" style="left:16px" width="16" height="26" viewBox="0 0 16 26"><path d="M13 2 L3 13 L13 24" fill="none" stroke="#222" stroke-width="3"/></svg>
  <ul><li>Halden</li><li>Corvex</li><li>Tamira</li><li>Norvale</li><li>Kestrel</li><li>Brightline</li><li>Aspenridge</li><li>Merrow</li><li>Verde</li></ul>
  <svg class="arrow" style="right:16px" width="16" height="26" viewBox="0 0 16 26"><path d="M3 2 L13 13 L3 24" fill="none" stroke="#222" stroke-width="3"/></svg>
</div>

<footer>
  <div class="abs footer"></div>
  <div class="abs footer-links">Home <span>|</span>News <span>|</span>About Us <span>|</span>Solutions <span>|</span>Contact Us <span>|</span>Members Area <span>|</span>Privacy Policy <span>|</span>Site Map.</div>
  <div class="abs social" aria-label="Social links"><span></span><span></span><span></span><span></span><span></span><span></span></div>
  <div class="abs copy">Copyright© 2014 National Copperfleece Breeders Guild . All rights reserved.</div>
  <div class="abs baseline"></div>
</footer>

</body>
</html>
```